life insurance quote website design for lepontdoriole.ca

the web site lepontdoriole.ca need a design. we dont like the actuel one but we are open at all new suggestion. visit us at lepontdoriole.ca and you will understand. the principal concurant is tarifsgarantisnord.ca, calculeo.ca, coutprotecfam.ca. We are a life insurance quote site. we found best price available in the canadien industrie. We absolutly want a design with our form in the front page on the top right side like our concurance, we use wordpress at this time. we want to be able to switch language. and to have a logic form. we want to be able to change the color for each type of insurance quote page.we also need a blog in it to post news. and the site will be SEO accurate.

Target Market(s)

Get client fill the quote form

Industry/Entity Type

Insurance

Number of Pages Required

3 page

Font styles to use
Sans Serif

Requirements
Must have
• logic form on the top right first page
• page template for product info stuff, contact, and who we are, blog
• French site
• custum color
Nice to have
• Wordpress design will be appréciate
• switch language english/french

```html
<!DOCTYPE html>
<html lang="en">
<head>
<meta charset="utf-8">
<title>Le Pont d'Oriole – Life Insurance Quotes</title>
<link rel="stylesheet" href="https://fonts.googleapis.com/css2?family=Open+Sans:wght@400;600;700;800&display=swap">
<style>
:root{
  --red:#d8232a;
  --navy:#2b3458;
  --navy-dark:#232b4a;
  --ink:#333;
  --muted:#777;
  --line:#e2e2e2;
  --panel:#f1f1f1;
  --teal:#2bb3b1;
  --orange:#f2a33a;
  --blue:#3a9fd8;
  --pink:#e8457a;
}
*{box-sizing:border-box;margin:0;padding:0}
html,body{width:1200px;height:3132px;overflow:hidden}
body{font-family:"Open Sans",Arial,sans-serif;color:var(--ink);background:#fff;position:relative;font-size:13px;line-height:1.55}
.wrap{position:absolute;left:56px;width:1088px}
a{color:inherit;text-decoration:none}

/* header */
.site-header{top:0;height:56px;display:flex;align-items:center;justify-content:space-between}
.brand{font-weight:800;color:var(--red);font-size:22px;line-height:1;letter-spacing:.5px;display:flex;align-items:center;gap:10px}
.brand .dot{width:14px;height:14px;background:var(--red)}
.top-info{display:flex;gap:30px;align-items:center;font-size:11px;color:var(--muted)}
.top-info .item{display:flex;align-items:center;gap:8px}
.top-info b{display:block;color:var(--red);font-size:9px;font-weight:700;text-transform:uppercase}
.icon-c{width:22px;height:22px;border-radius:50%;background:var(--red);display:flex;align-items:center;justify-content:center}
.main-nav{top:56px;height:40px;background:var(--red);display:flex}
.main-nav a{color:#fff;font-size:11px;font-weight:700;text-transform:uppercase;padding:0 34px;line-height:40px}
.main-nav a.active{background:var(--navy)}

/* hero */
.hero{top:96px;height:484px}
.hero-photo{position:absolute;inset:0;background:linear-gradient(180deg,#8fc3ea 0%,#c6e1f4 45%,#9fcf73 70%,#5e9b34 100%)}
.quote-form{position:absolute;right:12px;top:0;width:504px;height:484px;background:rgba(35,43,74,.93);padding:22px 34px;color:#fff}
.quote-form h2{color:var(--red);font-size:26px;font-weight:800;text-align:center;line-height:1.1}
.quote-form .sub{text-align:center;font-size:11px;color:#c9cde0;margin-bottom:16px}
.row{display:flex;gap:12px;margin-bottom:10px;align-items:center}
.lbl{font-size:12px;font-weight:600;width:110px}
.field{flex:1;height:30px;background:#fff;border-radius:2px;color:#999;font-size:11px;padding:0 10px;line-height:30px}
.section-lbl{font-size:13px;font-weight:700;margin:8px 0 8px}
.radios{display:flex;gap:40px;font-size:11px;color:#c9cde0}
.radios span::before{content:"";display:inline-block;width:10px;height:10px;border-radius:50%;border:1px solid #fff;margin-right:6px;vertical-align:-1px}
.captcha-row{display:flex;gap:14px;align-items:center;margin-top:16px}
.captcha{width:120px;height:44px;background:linear-gradient(90deg,#e9e9e9,#cfcfcf)}
.btn{background:var(--red);color:#fff;font-weight:700;font-size:13px;text-transform:uppercase;text-align:center}
.send{width:120px;height:44px;line-height:44px;margin-left:auto}

/* tiles */
.tiles{top:600px;height:226px;display:flex;gap:0}
.tile{flex:1;color:#fff;text-align:center}
.tile .top{height:190px;display:flex;flex-direction:column;align-items:center;justify-content:center;gap:14px}
.tile h3{font-size:20px;font-weight:800;line-height:1.1;text-transform:uppercase}
.tile .foot{height:36px;line-height:36px;background:#e8e8e8;color:#666;font-size:11px;font-weight:600;text-transform:uppercase;border-right:1px solid #fff}
.t1{background:var(--teal)}.t2{background:var(--orange)}.t3{background:var(--blue)}.t4{background:var(--pink)}

/* content */
.content{top:860px;width:844px}
.kicker{font-size:13px;font-weight:800;text-transform:uppercase;color:var(--navy)}
.headline{font-size:28px;font-weight:800;color:var(--red);text-transform:uppercase;line-height:1.15;margin-bottom:14px}
.content p{color:var(--muted);font-size:12px}
.checks{display:grid;grid-template-columns:1fr 1fr;gap:10px 20px;margin:22px 0;font-size:13px;font-weight:600}
.checks li{list-style:none;display:flex;gap:8px;align-items:center}
.block{margin-top:34px}
.block h2{font-size:22px;font-weight:700;color:var(--navy);margin-bottom:12px}
.block .body{display:flex;gap:22px}
.thumb{width:176px;height:150px;flex:none}
.more{display:inline-block;margin-top:10px;color:var(--blue);font-size:11px;font-weight:600}

/* sidebar */
.sidebar{top:860px;left:944px;width:200px}
.panel{background:var(--panel);margin-bottom:26px}
.panel h3{background:var(--navy);color:#fff;font-size:13px;font-weight:700;text-transform:uppercase;padding:12px;text-align:center}
.panel .in{padding:12px 14px;font-size:10px;color:#555;line-height:1.6}
.panel .in b{display:block;color:var(--navy);font-size:10px;text-transform:uppercase}
.towns li{list-style:none;border-bottom:1px solid #ddd;padding:2px 0}
.badge{height:150px;display:flex;align-items:center;justify-content:center}
.badge .shape{width:90px;height:90px;background:#d8d8d8;border-radius:50%}

/* news */
.news{top:2170px}
.news-head{display:flex;justify-content:space-between;align-items:center;margin-bottom:18px}
.news-head h2{font-size:26px;font-weight:800;color:var(--red);text-transform:uppercase}
.news-head a{font-size:11px;color:var(--blue);font-weight:600}
.cards{display:flex;gap:34px}
.card{flex:1;box-shadow:0 1px 4px rgba(0,0,0,.12)}
.card .img{height:190px}
.card .txt{padding:16px 20px;text-align:center;font-size:15px;font-weight:600;color:#444;line-height:1.35}
.card .meta{display:flex;justify-content:center;gap:30px;font-size:10px;color:var(--blue);padding-bottom:16px}

/* footer */
.site-footer{position:absolute;top:2690px;left:0;width:1200px;height:410px;background:var(--navy)}
.fcols{position:absolute;left:56px;top:50px;width:1088px;display:flex;gap:40px;color:#c9cde0;font-size:12px}
.fcols h4{color:var(--red);font-size:15px;font-weight:700;margin-bottom:14px}
.fcols li{list-style:none;line-height:2}
.fcol{flex:1}
.email-in{height:34px;background:#fff;color:#999;line-height:34px;padding:0 10px;font-size:11px;margin-bottom:10px}
.sub-btn{display:inline-block;padding:0 18px;height:30px;line-height:30px;font-size:11px}
.fphone{color:#fff;font-size:18px;font-weight:700}
.bottom-bar{position:absolute;top:3100px;left:0;width:1200px;height:32px;background:var(--navy-dark);color:#c9cde0;font-size:10px}
.bottom-bar .wrap{display:flex;justify-content:space-between;line-height:32px}
.bottom-bar nav a{margin-right:40px}
</style>
</head>
<body>

<header class="wrap site-header">
  <div class="brand"><span class="dot"></span>LE PONT D'ORIOLE</div>
  <div class="top-info">
    <div class="item"><div><b>Language</b>English ▾</div></div>
    <div class="item"><span class="icon-c"><svg width="12" height="12" viewBox="0 0 24 24"><path fill="#fff" d="M6.6 10.8a15 15 0 0 0 6.6 6.6l2.2-2.2c.3-.3.7-.4 1-.2 1.1.4 2.3.6 3.6.6.6 0 1 .4 1 1V20c0 .6-.4 1-1 1A17 17 0 0 1 3 4c0-.6.4-1 1-1h3.5c.6 0 1 .4 1 1 0 1.3.2 2.5.6 3.6.1.3 0 .7-.2 1z"/></svg></span><div><b>Call us</b>1-855-412-7730</div></div>
    <div class="item"><span class="icon-c"><svg width="12" height="12" viewBox="0 0 24 24"><path fill="#fff" d="M2 5h20v14H2zm2 2v.5l8 5 8-5V7z"/></svg></span><div><b>Email</b>contact@lepontdoriole.ca</div></div>
  </div>
</header>

<nav class="wrap main-nav">
  <a class="active" href="#">Home</a><a href="#">Products</a><a href="#">Submission</a><a href="#">Who are we?</a><a href="#">Blog</a><a href="#">Contact us</a>
</nav>

<section class="wrap hero">
  <div class="hero-photo" role="img" aria-label="Family running on a green meadow under a blue sky with a heart-shaped cloud"></div>
  <form class="quote-form">
    <h2>QUOTE REQUEST</h2>
    <div class="sub">Please fill out form &amp; call free 24/7</div>
    <div class="row"><span class="lbl">Product</span><span class="field">Type of insurance ▾</span></div>
    <div class="section-lbl">Applicant</div>
    <div class="row"><span class="field">First name</span><span class="field">Last name</span></div>
    <div class="row"><span class="field">Email</span><span class="field">Phone</span></div>
    <div class="row"><span class="field">Date of birth</span><span class="field">Smoker ▾</span></div>
    <div class="section-lbl">Co-Applicant</div>
    <div class="radios"><span>Add a co-applicant</span><span>I have read and accept the privacy policy</span></div>
    <div class="captcha-row">
      <div class="captcha" role="img" aria-label="Security verification code"></div>
      <span class="field" style="flex:none;width:140px">Enter code</span>
      <div class="btn send">Send</div>
    </div>
  </form>
</section>

<section class="wrap tiles">
  <div class="tile"><div class="top t1"><svg width="44" height="44" viewBox="0 0 24 24"><path fill="none" stroke="#fff" stroke-width="1.6" d="M12 20s-7-4.5-7-10a4 4 0 0 1 7-2.5A4 4 0 0 1 19 10c0 5.5-7 10-7 10z"/></svg><h3>Assurance<br>vie</h3></div><div class="foot">Beginning</div></div>
  <div class="tile"><div class="top t2"><svg width="44" height="44" viewBox="0 0 24 24"><circle cx="12" cy="12" r="9" fill="none" stroke="#fff" stroke-width="1.6"/><text x="12" y="16" text-anchor="middle" font-size="11" fill="#fff" font-family="Open Sans,sans-serif">$</text></svg><h3>Salaire</h3></div><div class="foot">Beginning</div></div>
  <div class="tile"><div class="top t3"><svg width="44" height="44" viewBox="0 0 24 24"><path fill="none" stroke="#fff" stroke-width="1.6" d="M3 11l9-7 9 7v9H3z"/></svg><h3>Hypothecaire</h3></div><div class="foot">Beginning</div></div>
  <div class="tile"><div class="top t4"><svg width="44" height="44" viewBox="0 0 24 24"><path fill="none" stroke="#fff" stroke-width="1.6" d="M10 3h4v7h7v4h-7v7h-4v-7H3v-4h7z"/></svg><h3>Maladies<br>graves</h3></div><div class="foot">Beginning</div></div>
</section>

<main class="wrap content">
  <div class="kicker">Online life insurance submission</div>
  <h1 class="headline">Find the best insurance at the best price!</h1>
  <p>Whether you are looking for life insurance, mortgage insurance or loan protection, we compare the top Canadian insurers to find the coverage that truly fits your family. Our licensed advisors review every option, explain each guarantee in plain words and help you pick a plan with a premium that stays fair over time. Fill out the quick form above, receive several quotes at no cost and choose with confidence. Our service is free, confidential and available in French and English across the province.</p>
  <ul class="checks">
    <li><svg width="14" height="14" viewBox="0 0 24 24"><path fill="none" stroke="#3aa34a" stroke-width="3" d="M4 12l5 5L20 6"/></svg>Permanent life insurance - term life insurance</li>
    <li><svg width="14" height="14" viewBox="0 0 24 24"><path fill="none" stroke="#3aa34a" stroke-width="3" d="M4 12l5 5L20 6"/></svg>Mortgage insurance - loans</li>
    <li><svg width="14" height="14" viewBox="0 0 24 24"><path fill="none" stroke="#3aa34a" stroke-width="3" d="M4 12l5 5L20 6"/></svg>Disability insurance - disability insurance</li>
    <li><svg width="14" height="14" viewBox="0 0 24 24"><path fill="none" stroke="#3aa34a" stroke-width="3" d="M4 12l5 5L20 6"/></svg>Critical illness insurance</li>
  </ul>

  <section class="block">
    <h2>How to proceed?</h2>
    <div class="body">
      <div class="thumb" role="img" aria-label="Father lifting his child in a sunny park" style="background:linear-gradient(135deg,#bfdff0,#e8d7b8)"></div>
      <div><p>Simply fill in the insurance quote form above, stating your insurance category, your age and your smoker status. As soon as we receive it, we will send your request to several insurers at once and compare the prices offered. Within one business day, an advisor calls you back with the best rates found, answers your questions and helps you complete the application if you wish to go ahead with one of the proposals.</p><a class="more" href="#">Read more »</a></div>
    </div>
  </section>

  <section class="block">
    <h2>Competent financial advisors Security</h2>
    <div class="body">
      <div class="thumb" role="img" aria-label="Advisor in a suit shaking hands with a client" style="background:linear-gradient(135deg,#6d7a8c,#cfd6df)"></div>
      <div><p>All our advisors hold a valid license and follow strict ethical rules. They work for you, not for one insurer, which means the advice you receive is objective and focused on your needs. Your personal information stays protected at every step, and no contract is ever signed without your clear approval. Take the time you need; we are here to guide you before, during and after the purchase of your policy.</p><a class="more" href="#">Read more »</a></div>
    </div>
  </section>

  <section class="block">
    <h2>The importance of not overpaying</h2>
    <div class="body">
      <div class="thumb" role="img" aria-label="Happy family lying together on the grass" style="background:linear-gradient(135deg,#f2c9a0,#9cc97a)"></div>
      <div><p>Reducing monthly or annual premiums leaves more room in your budget for the things that matter. Prices for identical coverage can vary a lot from one company to another, so comparing is essential. With a simple request you see the real market and avoid paying for extras you do not need. Saving a little every month adds up to a large amount over the life of a policy.</p><a class="more" href="#">Read more »</a></div>
    </div>
  </section>
</main>

<aside class="wrap sidebar">
  <div class="panel">
    <h3>Our offices</h3>
    <div class="in">
      <b>The head office</b>740 boul. Riviera, Laval, QC H7N 0A1
      <b style="margin-top:10px">Towns</b>
      <ul class="towns"><li>Montréal</li><li>Québec</li><li>Sherbrooke</li><li>Laval</li><li>Rimouski</li><li>Saint-Hyacinthe</li><li>Trois-Rivières</li><li>Gatineau</li><li>Longueuil</li><li>Saguenay</li><li>Granby</li><li>Saint-Jérôme</li><li>Victoriaville</li><li>Joliette</li><li>Shawinigan</li><li>La Tuque</li></ul>
    </div>
  </div>
  <div class="panel">
    <h3>Hours of operation</h3>
    <div class="in">
      <b>Our hours of operation</b><br>
      Monday to Friday<br><b>9am to 9pm</b><br>
      Saturday<br><b>10am to 4pm</b><br>
      Toll free<br><b>1-855-412-7730</b><br>
      Email<br><b style="text-transform:none">contact@lepontdoriole.ca</b>
    </div>
  </div>
  <div class="panel badge"><div class="shape"></div></div>
</aside>

<section class="wrap news">
  <div class="news-head"><h2>Latest news</h2><a href="#">View all »</a></div>
  <div class="cards">
    <article class="card"><div class="img" role="img" aria-label="Grandparents and children smiling outdoors" style="background:linear-gradient(135deg,#a8d08d,#e9dcc0)"></div><div class="txt">Lorem ipsum dolor sit amet conse ctetur adipiscing elit.</div><div class="meta"><span>Jane Smith</span><span>April 23, 2016</span></div></article>
    <article class="card"><div class="img" role="img" aria-label="Child jumping under a bright blue sky" style="background:linear-gradient(180deg,#4f9fe0,#cfe6f7)"></div><div class="txt">Lorem ipsum dolor sit amet conse ctetur adipiscing elit.</div><div class="meta"><span>Jane Smith</span><span>April 23, 2016</span></div></article>
    <article class="card"><div class="img" role="img" aria-label="Couple with a dog in a green park" style="background:linear-gradient(135deg,#7fb85a,#e6d3b5)"></div><div class="txt">Lorem ipsum dolor sit amet conse ctetur adipiscing elit.</div><div class="meta"><span>Jane Smith</span><span>April 23, 2016</span></div></article>
  </div>
</section>

<footer class="site-footer">
  <div class="fcols">
    <div class="fcol"><h4>Navigation</h4><ul><li>Home</li><li>Products</li><li>Submission</li><li>Who are we?</li><li>Contact us</li></ul></div>
    <div class="fcol"><h4>Information</h4><ul><li>Legal notice</li><li>All stories</li><li>Newsletter</li><li>Privacy policy</li><li>Terms of service</li></ul></div>
    <div class="fcol"><h4>Newsletter</h4><div class="email-in">Enter your email</div><span class="btn sub-btn">Subscribe</span></div>
    <div class="fcol"><h4>Contact us</h4><div class="fphone">1-855-412-7730</div><div>contact@lepontdoriole.ca</div></div>
  </div>
</footer>
<div class="bottom-bar"><div class="wrap"><nav><a href="#">Terms of use</a><a href="#">Privacy policy</a><a href="#">Site map</a></nav><span>© 2016 - Le Pont d'Oriole. All rights reserved.</span></div></div>

</body>
</html>
```